House-share and Room Rental Website (With Focus on the Bedroom Landing Page)

Looking for website design for our House-share (executive accommodation) and room rental business.

Our company name is: Lodgivo could also be written as LodGivo or lodgivo. Either is fine .. just looking for a nice clean catchy logo to go with the design.

EXAMPLES
These are examples of other websites in this field that are doing well. this is a kind of baseline.
https://nestpartners-example.com.au/
https://www.bunkora-example.com/
https://www.dwelzy-example.com/
https://www.habiquo-example.net/
https://www.cohabiscout-example.com.au/

Our business model is to rent rooms to people looking for high-quality accommodation. We fill the gap between those looking to rent rooms and those with rooms to rent. However, our model is slightly different from those already on the market as we looking to fill a massive gap in the market delivering upmarket rooms for rent.(Executive Accommodation) also in the back end will be coupled with a self management process in the back end.

We offer executive style accommodation that stands out above the rest. With special extras like fire safety.. and management processes that create happier homes. We are looking for a web design package that can help us grow and scale our business. We need a design that is captivating

Our MAIN focus is having a room landing page that stands out from the rest... The core of our business will rely on the promotion of the rooms in a share house... so the whole design relies on the BEDROOM landing page to drive results.

Target Market(s)

We have 2 markets we are aiming at ... the first market is people offering rooms to rent who want the highest rental return. The second market is people looking to rent safe, high-quality rooms, in houses that are well managed and looked after.

Industry/Entity Type

Share Economy

Logo Text

LodGivo

Number of Pages Required

5+ page

Font styles to use
Sans Serif

Colors
3276b5

Requirements
Must have
• A messaging system whereby we can create direct communication between those offering rooms and those looking for rooms.
• A call to action that says " Schedule an Inspection"
• Landing page for promoting rooms
• A home page for showing stock.
• Profile page for those selling rooms
• Profile page for those looking for rooms.
• A scheduling calendar for booking inspections
Nice to have
• Pages where new residents can lock in a room.. pay bond and rents.. and sign contracts
• Notifications
• SMS capabilities in the backend.
Should not have
• No script or handwriting fonts.

```html
<!DOCTYPE html>
<html lang="en">
<head>
<meta charset="utf-8">
<title>Lodgivo – Room Listing</title>
<link rel="stylesheet" href="https://fonts.googleapis.com/css2?family=Questrial&family=Open+Sans:wght@400;600;700&display=swap">
<style>
:root{
  --blue:#1d70bb;
  --blue-dark:#175e9f;
  --red:#d0021b;
  --ink:#222;
  --text:#444;
  --muted:#777;
  --line:#e6e6e6;
  --footer:#232323;
  --footer-field:#3a3a3a;
  --star:#f5b301;
  --white:#fff;
  --cal:#f4f4f4;
}
*{box-sizing:border-box;margin:0;padding:0}
html,body{width:1200px;height:3046px;overflow:hidden}
body{position:relative;background:var(--white);font-family:"Open Sans",Arial,sans-serif;color:var(--text);font-size:11px}
.abs{position:absolute}
.head-font{font-family:"Questrial","Open Sans",sans-serif}
.stars{color:var(--star);letter-spacing:1px;font-size:11px}
.photo{border-radius:2px}

/* header */
.site-header{left:0;top:0;width:1200px;height:98px}
.menu-grid{left:78px;top:36px}
.lang{left:118px;top:38px;display:flex;align-items:center;gap:6px;font-size:11px;color:#333}
.flag{width:14px;height:9px;background:linear-gradient(#b22234 0 50%,#fff 50% 100%);border:1px solid #ccc;position:relative}
.flag::before{content:"";position:absolute;left:0;top:0;width:6px;height:5px;background:#3c3b6e}
.brand{display:flex;align-items:center;gap:8px;font-family:"Questrial",sans-serif;font-size:30px;color:var(--blue)}
.brand-dot{width:30px;height:30px;border:4px solid var(--blue);border-radius:50%}
.site-header .brand{left:510px;top:26px}
.btn-post{left:918px;top:30px;width:128px;height:32px;background:var(--blue);color:#fff;border-radius:5px;font-size:12px;display:flex;align-items:center;justify-content:center}
.btn-login{left:1056px;top:30px;width:64px;height:32px;border:1px solid #bbb;border-radius:5px;font-size:12px;color:#333;display:flex;align-items:center;justify-content:center}
.hero{left:0;top:98px;width:1200px;height:422px;background:linear-gradient(100deg,#c9b79a 0%,#6b3a26 30%,#e9e2d3 55%,#f3efe7 70%,#8aa9b8 82%,#5a3a2a 100%)}

/* room detail */
.main-photo{left:79px;top:612px;width:522px;height:363px;background:linear-gradient(180deg,#5a3d2a 0%,#8a6a4e 40%,#e8e0d2 70%,#6e4e36 100%)}
.thumb{top:990px;width:118px;height:100px}
.t1{left:79px;background:linear-gradient(135deg,#3b2a1e,#a07a52)}
.t2{left:213px;background:linear-gradient(135deg,#4a3628,#1e1612)}
.t3{left:347px;background:linear-gradient(135deg,#6b5644,#2e241d)}
.t4{left:483px;background:linear-gradient(135deg,#efe9e0,#8c7b6a)}
.room-info{left:637px;top:624px;width:480px}
.room-type{font-size:11px;color:#333}
.offer{font-family:"Questrial",sans-serif;font-size:19px;color:var(--red);margin-top:5px;font-weight:700}
.room-address{font-family:"Questrial",sans-serif;font-size:20px;color:var(--ink);line-height:26px;margin-top:3px;font-weight:700;width:320px}
.room-meta{font-size:11px;color:#444;margin-top:6px}
.room-facts{font-size:11px;color:#333;margin-top:12px;display:flex;gap:10px}
.feature{margin-top:18px}
.feature h3{font-family:"Questrial",sans-serif;font-size:19px;color:var(--ink);display:flex;align-items:center;gap:10px;font-weight:600}
.feature p{font-size:11px;line-height:16px;color:#444;margin-top:10px;width:480px}
.host{left:1048px;top:644px;width:80px;text-align:center;font-size:11px;color:#333}
.host-photo{width:52px;height:52px;border-radius:50%;margin:0 auto 8px;background:radial-gradient(circle,#e8c7a8,#8a5a3e)}
.divider{left:79px;width:1041px;height:1px;background:var(--line)}

/* amenities */
.section-title{font-family:"Questrial",sans-serif;font-size:23px;color:var(--ink)}
.amen-title{left:0;width:1200px;top:1180px;text-align:center}
.amenities{left:96px;top:1255px;width:1024px;display:flex;justify-content:space-between}
.amenity{display:flex;align-items:center;gap:9px;font-size:11px;color:#333}
.show-all{left:0;width:1200px;top:1344px;text-align:center;font-size:11px;font-weight:600;color:#333}
.show-all span{border-bottom:1px solid #333;padding-bottom:1px}

/* cards */
.card{border:1px solid #ddd;border-radius:6px;box-shadow:0 2px 6px rgba(0,0,0,.08);background:#fff}
.review-card{left:83px;top:1458px;width:480px;height:502px;text-align:center}
.review-card h2{font-family:"Questrial",sans-serif;font-size:23px;color:var(--ink);margin-top:36px;font-weight:400}
.reviewer-photo{width:122px;height:122px;border-radius:50%;margin:18px auto 0;background:radial-gradient(circle at 50% 40%,#c79a7a,#5d4a3e 70%,#2f4f7a)}
.reviewer{font-size:18px;font-weight:700;color:var(--ink);margin-top:28px}
.role{color:var(--blue);font-size:11px;margin-top:4px}
.review-card .stars{margin-top:6px;display:block}
.review-text{font-size:11px;line-height:15px;color:#444;width:400px;margin:22px auto 0}
.read-more{font-size:12px;color:#333;margin-top:14px;display:flex;justify-content:center;align-items:center;gap:6px}
.dots{display:flex;justify-content:center;gap:5px;margin-top:18px}
.dots i{width:5px;height:5px;border-radius:50%;background:#333}
.dots i:first-child{background:var(--blue)}
.booking-card{left:637px;top:1458px;width:483px;height:502px;padding:22px 26px}
.price{font-size:19px;color:var(--red);font-weight:700;font-family:"Questrial",sans-serif}
.dates{display:flex;justify-content:space-between;margin-top:38px}
.date-col{width:200px}
.date-head{display:flex;justify-content:space-between;align-items:center;font-family:"Questrial",sans-serif;font-size:18px;color:var(--ink);padding-right:8px}
.calendar{margin-top:16px;background:var(--cal);height:170px;padding:12px 10px;font-size:8px;color:#333}
.cal-top{display:flex;justify-content:space-between;font-size:9px;margin-bottom:8px;padding:0 4px}
.cal-top b{font-weight:600;flex:1;text-align:center}
.cal-grid{display:grid;grid-template-columns:repeat(7,1fr);row-gap:10px;text-align:left;padding-left:4px}
.cal-grid .dow{color:#666}
.guests-label{font-size:11px;color:#333;margin-top:20px}
.select{margin-top:10px;height:46px;border:1px solid #ccc;border-radius:5px;display:flex;align-items:center;justify-content:space-between;padding:0 14px 0 26px;font-size:11px;color:#333}
.btn-book{margin-top:28px;height:46px;background:var(--blue);color:#fff;border-radius:4px;font-size:13px;font-weight:600;display:flex;align-items:center;justify-content:center;letter-spacing:.3px}

/* related */
.related-title{left:79px;top:2076px}
.pager{left:1088px;top:2082px;display:flex;gap:12px}
.room-card{top:2140px;width:327px;height:415px;background:#fff;box-shadow:0 1px 5px rgba(0,0,0,.1)}
.room-img{height:215px;position:relative}
.r1 .room-img{background:linear-gradient(135deg,#2e3d5a,#c9c3b8 60%,#6b6a72)}
.r2 .room-img{background:linear-gradient(135deg,#f1ede6,#d8cbb8 60%,#9a8a76)}
.r3 .room-img{background:linear-gradient(135deg,#2a2420,#8a5a3a 50%,#c23a2e 65%,#3a2e26)}
.checkbox{position:absolute;left:8px;top:8px;width:15px;height:15px;border:1px solid #fff;border-radius:2px}
.price-tag{position:absolute;left:0;bottom:10px;height:30px;width:70px;background:var(--blue);color:#fff;font-size:17px;font-weight:700;display:flex;align-items:center;padding-left:8px;clip-path:polygon(0 0,84% 0,100% 50%,84% 100%,0 100%)}
.room-body{padding:12px 16px 0}
.room-name{font-family:"Questrial",sans-serif;font-size:15px;color:var(--blue);font-weight:700;padding-bottom:10px;border-bottom:1px solid var(--line)}
.room-loc{display:flex;align-items:center;gap:8px;font-size:11px;color:#444;margin-top:12px}
.room-stats{display:flex;justify-content:space-between;margin-top:14px;padding:0 18px 0 14px}
.stat{font-size:10px;color:#444;text-align:center}
.stat-top{display:flex;align-items:flex-start;gap:3px;justify-content:center;font-size:10px}
.btn-browse{width:104px;height:28px;margin:10px auto 0;background:#3a3a3a;color:#fff;font-size:10px;border-radius:3px;display:flex;align-items:center;justify-content:center}

/* footer */
.site-footer{left:0;top:2636px;width:1200px;height:352px;background:var(--footer);color:#ddd}
.site-footer .brand{position:absolute;left:79px;top:82px;font-size:26px;color:var(--blue)}
.site-footer .brand-dot{width:26px;height:26px}
.foot-about{position:absolute;left:79px;top:158px;width:210px;font-size:12px;line-height:20px;color:#eee}
.socials{position:absolute;left:79px;top:250px;display:flex;gap:11px}
.socials i{width:22px;height:22px;border:1px solid #aaa;border-radius:50%}
.socials i:first-child{background:var(--blue);border-color:var(--blue)}
.foot-col h4{font-family:"Questrial",sans-serif;font-size:16px;color:#fff;font-weight:400}
.foot-col h4::after{content:"";display:block;width:64px;height:3px;background:#fff;margin-top:10px}
.links{position:absolute;left:372px;top:70px}
.links ul{list-style:none;margin-top:22px}
.links li{font-size:11px;color:#ddd;height:24px;display:flex;align-items:center;gap:18px}
.links li::before{content:"›";font-size:14px;color:#ccc}
.contact{position:absolute;left:577px;top:66px}
.contact h4::after{display:none}
.contact-row{display:flex;gap:12px;font-size:12px;line-height:28px;color:#eee;margin-top:4px}
.contact-row svg{margin-top:8px;flex:none}
.quick{position:absolute;left:890px;top:70px;width:230px}
.fields{display:flex;gap:10px;margin-top:22px}
.field{background:var(--footer-field);height:28px;font-size:11px;color:#ccc;padding:6px 10px;flex:1}
.field.msg{height:62px;margin-top:8px}
.btn-send{margin:8px 0 0 auto;width:128px;height:30px;background:var(--blue);color:#fff;border-radius:4px;font-size:12px;font-weight:600;display:flex;align-items:center;justify-content:center}
.bottom-bar{left:0;top:2988px;width:1200px;height:58px;background:var(--blue);color:#fff;font-size:12px;display:flex;align-items:center;justify-content:space-between;padding:0 79px}
.cards{display:flex;gap:8px}
.cards i{width:36px;height:22px;background:#fff;border-radius:3px;opacity:.9}
</style>
</head>
<body>

<header class="abs site-header">
  <svg class="abs menu-grid" width="22" height="22" viewBox="0 0 22 22" fill="#333">
    <rect x="0" y="0" width="5" height="5"/><rect x="8.5" y="0" width="5" height="5"/><rect x="17" y="0" width="5" height="5"/>
    <rect x="0" y="8.5" width="5" height="5"/><rect x="8.5" y="8.5" width="5" height="5"/><rect x="17" y="8.5" width="5" height="5"/>
    <rect x="0" y="17" width="5" height="5"/><rect x="8.5" y="17" width="5" height="5"/><rect x="17" y="17" width="5" height="5"/>
  </svg>
  <div class="abs lang"><span class="flag"></span>Eng ▾</div>
  <div class="abs brand"><span class="brand-dot"></span>Lodgivo</div>
  <div class="abs btn-post">Post Your Room</div>
  <div class="abs btn-login">Log In</div>
</header>

<div class="abs hero" role="img" aria-label="Bright bedroom with a dark wooden bed, armchairs and tall windows"></div>

<div class="abs photo main-photo" role="img" aria-label="Ornate bedroom with a carved wooden headboard and hanging lanterns"></div>
<div class="abs thumb t1" role="img" aria-label="Living room view"></div>
<div class="abs thumb t2" role="img" aria-label="Lounge with television"></div>
<div class="abs thumb t3" role="img" aria-label="Study with bookshelves"></div>
<div class="abs thumb t4" role="img" aria-label="Modern kitchen"></div>

<section class="abs room-info">
  <div class="room-type">Private Room in Apartment</div>
  <div class="offer">Special Offer</div>
  <h1 class="room-address">48 Harbour Lane, Port Westhaven, VIC 3299</h1>
  <div class="room-meta">Size of Room – 9' x 9' (2.74 x 2.75m)</div>
  <div class="room-meta"><span class="stars">★★★★★</span> (200 Views)</div>
  <div class="room-facts"><span>2 Guests</span><span>1 Bedroom</span><span>1 Bed</span><span>1.5 Shared Baths</span></div>
  <div class="feature" style="margin-top:26px">
    <h3><svg width="20" height="18" viewBox="0 0 20 18" fill="#222"><path d="M13 0l3 2-5 7 2 2-2 2L6 8l2-2 2 2z"/><path d="M5 9l6 6-2 3H0l2-3 1 1 1-2z"/></svg>Sparkling clean</h3>
    <p>Lorem Ipsum is simply dummy text of the printing and typesetting industry. Lorem Ipsum has been the industry's standard dummy text ever since the 1500s</p>
  </div>
  <div class="feature">
    <h3><svg width="18" height="18" viewBox="0 0 18 18" fill="#222"><path d="M9 0l9 8h-3v10H3V8H0z"/><rect x="7" y="11" width="4" height="7" fill="#fff"/></svg>Self check-in</h3>
    <p>Lorem Ipsum is simply dummy text of the printing and typesetting industry. Lorem Ipsum has been the industry's standard dummy text ever since the 1500s</p>
  </div>
  <div class="feature">
    <h3><svg width="22" height="14" viewBox="0 0 22 14" fill="#222"><rect x="0" y="4" width="3" height="6"/><rect x="3" y="1" width="3" height="12"/><rect x="6" y="6" width="10" height="2"/><rect x="16" y="1" width="3" height="12"/><rect x="19" y="4" width="3" height="6"/></svg>Gym</h3>
    <p>Lorem Ipsum is simply dummy text of the printing and typesetting industry.</p>
  </div>
</section>
<div class="abs host"><div class="host-photo" role="img" aria-label="Host profile photo"></div>Marissa</div>

<div class="abs divider" style="top:1140px"></div>

<h2 class="abs section-title amen-title">ROOM Amenities</h2>
<div class="abs amenities">
  <div class="amenity"><svg width="38" height="34" viewBox="0 0 38 34" fill="none" stroke="#222" stroke-width="2.5"><rect x="2" y="9" width="34" height="23" rx="2"/><path d="M12 2l7 7 8-7"/><rect x="7" y="14" width="20" height="13" fill="#222"/></svg>TV</div>
  <div class="amenity"><svg width="32" height="36" viewBox="0 0 32 36" fill="#222"><rect x="0" y="0" width="32" height="36"/><rect x="4" y="4" width="11" height="8" fill="#fff"/><rect x="17" y="4" width="11" height="8" fill="#fff"/><rect x="4" y="14" width="11" height="8" fill="#fff"/><rect x="17" y="14" width="11" height="8" fill="#fff"/><rect x="4" y="24" width="24" height="8" fill="#fff"/></svg>Storage Space</div>
  <div class="amenity"><svg width="44" height="36" viewBox="0 0 44 36" fill="#222"><circle cx="14" cy="5" r="4"/><path d="M8 11h12l2 12h-6l-2 13h-4l1-13H8z"/><rect x="18" y="16" width="26" height="3"/><rect x="38" y="19" width="3" height="17"/><rect x="28" y="4" width="12" height="10"/><rect x="0" y="22" width="3" height="14"/></svg>Study Desk</div>
  <div class="amenity"><svg width="44" height="34" viewBox="0 0 44 34" fill="#222"><rect x="0" y="2" width="30" height="20" rx="1"/><rect x="3" y="5" width="24" height="14" fill="#fff"/><rect x="12" y="22" width="6" height="6"/><rect x="6" y="28" width="18" height="3"/><rect x="33" y="2" width="11" height="29"/><rect x="35" y="6" width="7" height="2" fill="#fff"/></svg>Workstation</div>
  <div class="amenity"><svg width="40" height="32" viewBox="0 0 40 32" fill="#222"><path d="M0 14h40v4c0 6-4 10-10 10H10C4 28 0 24 0 18z"/><rect x="6" y="28" width="3" height="4"/><rect x="31" y="28" width="3" height="4"/><path d="M4 14V5a4 4 0 018 0" fill="none" stroke="#222" stroke-width="2.5"/><circle cx="20" cy="6" r="1.5"/><circle cx="26" cy="4" r="1.5"/><circle cx="24" cy="9" r="1.5"/></svg>Ensuite shower</div>
  <div class="amenity"><svg width="44" height="34" viewBox="0 0 44 34" fill="#222"><path d="M2 0v10a3 3 0 003 3v21h2V13a3 3 0 003-3V0H8v8H7V0H5v8H4V0z"/><circle cx="22" cy="17" r="13"/><circle cx="22" cy="17" r="9" fill="#fff"/><path d="M38 0c4 4 4 12 0 16v18h2V0z"/></svg>Kitchenette</div>
</div>
<div class="abs show-all"><span>Show all 12 Amenities</span></div>

<div class="abs divider" style="top:1402px"></div>

<section class="abs card review-card">
  <h2>Reviews</h2>
  <div class="reviewer-photo" role="img" aria-label="Reviewer profile photo"></div>
  <div class="reviewer">Daniel Reeve</div>
  <div class="role">Director</div>
  <span class="stars">★★★★★</span>
  <p class="review-text">Lorem Ipsum is simply dummy text of the printing and typesetting industry. Loremhas been the industry's standard dummy text ever in the since the 1500s</p>
  <div class="read-more">Read More... <svg width="13" height="13" viewBox="0 0 13 13" fill="none" stroke="#333" stroke-width="1.3"><circle cx="6.5" cy="6.5" r="5.8"/><path d="M5.3 4l2.5 2.5-2.5 2.5"/></svg></div>
  <div class="dots"><i></i><i></i><i></i></div>
</section>

<section class="abs card booking-card">
  <div class="price">$250</div>
  <div class="room-meta" style="margin-top:2px"><span class="stars">★★★★★</span> (200 Views)</div>
  <div class="dates">
    <div class="date-col">
      <div class="date-head">Check In <svg width="12" height="8" viewBox="0 0 12 8" fill="none" stroke="#222" stroke-width="2"><path d="M1 1l5 5 5-5"/></svg></div>
      <div class="calendar">
        <div class="cal-top"><span>‹</span><b>February 2019</b><span></span></div>
        <div class="cal-grid">
          <span class="dow">SU</span><span class="dow">MO</span><span class="dow">TU</span><span class="dow">WE</span><span class="dow">TH</span><span class="dow">FR</span><span class="dow">SA</span>
          <span></span><span></span><span></span><span></span><span></span><span>1</span><span>2</span>
          <span>3</span><span>4</span><span>5</span><span>6</span><span>7</span><span>8</span><span>9</span>
          <span>10</span><span>11</span><span>12</span><span>13</span><span>14</span><span>15</span><span>16</span>
          <span>17</span><span>18</span><span>19</span><span>20</span><span>21</span><span>22</span><span>23</span>
          <span>24</span><span>25</span><span>26</span><span>27</span><span>28</span><span></span><span></span>
        </div>
      </div>
    </div>
    <div class="date-col">
      <div class="date-head">Check out <svg width="12" height="8" viewBox="0 0 12 8" fill="none" stroke="#222" stroke-width="2"><path d="M1 1l5 5 5-5"/></svg></div>
      <div class="calendar">
        <div class="cal-top"><span>‹</span><b>February 2019</b><span></span></div>
        <div class="cal-grid">
          <span class="dow">SU</span><span class="dow">MO</span><span class="dow">TU</span><span class="dow">WE</span><span class="dow">TH</span><span class="dow">FR</span><span class="dow">SA</span>
          <span></span><span></span><span></span><span></span><span></span><span>1</span><span>2</span>
          <span>3</span><span>4</span><span>5</span><span>6</span><span>7</span><span>8</span><span>9</span>
          <span>10</span><span>11</span><span>12</span><span>13</span><span>14</span><span>15</span><span>16</span>
          <span>17</span><span>18</span><span>19</span><span>20</span><span>21</span><span>22</span><span>23</span>
          <span>24</span><span>25</span><span>26</span><span>27</span><span>28</span><span></span><span></span>
        </div>
      </div>
    </div>
  </div>
  <div class="guests-label">Guests</div>
  <div class="select">3 Guests <svg width="14" height="9" viewBox="0 0 14 9" fill="none" stroke="#222" stroke-width="2.2"><path d="M1 1l6 6 6-6"/></svg></div>
  <div class="btn-book">REQUEST TO BOOK</div>
</section>

<div class="abs divider" style="top:2043px"></div>

<h2 class="abs section-title related-title">Related Room</h2>
<div class="abs pager">
  <svg width="8" height="13" viewBox="0 0 8 13" fill="none" stroke="#222" stroke-width="2.2"><path d="M7 1L2 6.5 7 12"/></svg>
  <svg width="8" height="13" viewBox="0 0 8 13" fill="none" stroke="var(--blue)" stroke-width="2.2"><path d="M1 1l5 5.5L1 12"/></svg>
</div>

<article class="abs room-card r1" style="left:79px">
  <div class="room-img" role="img" aria-label="Bedroom with grey bed and blue wall"><span class="checkbox"></span><span class="price-tag">$250</span></div>
  <div class="room-body">
    <div class="room-name">Luxurious &amp; Stunning Room</div>
    <div class="room-loc"><svg width="11" height="14" viewBox="0 0 11 14" fill="none" stroke="#666" stroke-width="1.4"><path d="M5.5 13S1 8 1 5a4.5 4.5 0 019 0c0 3-4.5 8-4.5 8z"/><circle cx="5.5" cy="5" r="1.6"/></svg>17 Seacrest Road, Lindmore, Australia</div>
    <div class="room-stats">
      <div class="stat"><div class="stat-top"><svg width="20" height="16" viewBox="0 0 20 16" fill="none" stroke="#333" stroke-width="1.5"><path d="M1 7l9-6 9 6v8H1z"/><rect x="7" y="9" width="6" height="6"/></svg>2</div>Rooms</div>
      <div class="stat"><div class="stat-top"><svg width="22" height="14" viewBox="0 0 22 14" fill="#333"><rect x="0" y="0" width="2" height="14"/><rect x="2" y="7" width="20" height="4"/><rect x="20" y="4" width="2" height="10"/><rect x="4" y="3" width="6" height="4" rx="1"/></svg>4</div>Bedrooms</div>
      <div class="stat"><div class="stat-top"><svg width="16" height="16" viewBox="0 0 16 16" fill="#333"><rect x="0" y="0" width="7" height="6"/><path d="M2 8h14v2a5 5 0 01-5 5H6a4 4 0 01-4-4z"/></svg>2</div>Bath</div>
    </div>
    <div class="btn-browse">Browse</div>
  </div>
</article>

<article class="abs room-card r2" style="left:434px">
  <div class="room-img" role="img" aria-label="White canopy bedroom with ceiling fan"><span class="checkbox"></span><span class="price-tag">$250</span></div>
  <div class="room-body">
    <div class="room-name">Luxurious &amp; Stunning Room</div>
    <div class="room-loc"><svg width="11" height="14" viewBox="0 0 11 14" fill="none" stroke="#666" stroke-width="1.4"><path d="M5.5 13S1 8 1 5a4.5 4.5 0 019 0c0 3-4.5 8-4.5 8z"/><circle cx="5.5" cy="5" r="1.6"/></svg>17 Seacrest Road, Lindmore, Australia</div>
    <div class="room-stats">
      <div class="stat"><div class="stat-top"><svg width="20" height="16" viewBox="0 0 20 16" fill="none" stroke="#333" stroke-width="1.5"><path d="M1 7l9-6 9 6v8H1z"/><rect x="7" y="9" width="6" height="6"/></svg>2</div>Rooms</div>
      <div class="stat"><div class="stat-top"><svg width="22" height="14" viewBox="0 0 22 14" fill="#333"><rect x="0" y="0" width="2" height="14"/><rect x="2" y="7" width="20" height="4"/><rect x="20" y="4" width="2" height="10"/><rect x="4" y="3" width="6" height="4" rx="1"/></svg>4</div>Bedrooms</div>
      <div class="stat"><div class="stat-top"><svg width="16" height="16" viewBox="0 0 16 16" fill="#333"><rect x="0" y="0" width="7" height="6"/><path d="M2 8h14v2a5 5 0 01-5 5H6a4 4 0 01-4-4z"/></svg>2</div>Bath</div>
    </div>
    <div class="btn-browse">Browse</div>
  </div>
</article>

<article class="abs room-card r3" style="left:792px">
  <div class="room-img" role="img" aria-label="Warm-lit bedroom with red cushions"><span class="checkbox"></span><span class="price-tag">$250</span></div>
  <div class="room-body">
    <div class="room-name">Luxurious &amp; Stunning Room</div>
    <div class="room-loc"><svg width="11" height="14" viewBox="0 0 11 14" fill="none" stroke="#666" stroke-width="1.4"><path d="M5.5 13S1 8 1 5a4.5 4.5 0 019 0c0 3-4.5 8-4.5 8z"/><circle cx="5.5" cy="5" r="1.6"/></svg>17 Seacrest Road, Lindmore, Australia</div>
    <div class="room-stats">
      <div class="stat"><div class="stat-top"><svg width="20" height="16" viewBox="0 0 20 16" fill="none" stroke="#333" stroke-width="1.5"><path d="M1 7l9-6 9 6v8H1z"/><rect x="7" y="9" width="6" height="6"/></svg>2</div>Rooms</div>
      <div class="stat"><div class="stat-top"><svg width="22" height="14" viewBox="0 0 22 14" fill="#333"><rect x="0" y="0" width="2" height="14"/><rect x="2" y="7" width="20" height="4"/><rect x="20" y="4" width="2" height="10"/><rect x="4" y="3" width="6" height="4" rx="1"/></svg>4</div>Bedrooms</div>
      <div class="stat"><div class="stat-top"><svg width="16" height="16" viewBox="0 0 16 16" fill="#333"><rect x="0" y="0" width="7" height="6"/><path d="M2 8h14v2a5 5 0 01-5 5H6a4 4 0 01-4-4z"/></svg>2</div>Bath</div>
    </div>
    <div class="btn-browse">Browse</div>
  </div>
</article>

<footer class="abs site-footer">
  <div class="brand"><span class="brand-dot"></span>Lodgivo</div>
  <p class="foot-about">Lorem Ipsum is simply dummy text of the printing and types tysietting industry...</p>
  <div class="socials"><i></i><i></i><i></i><i></i><i></i></div>

  <div class="foot-col links">
    <h4>Useful links</h4>
    <ul><li>Login</li><li>Register</li><li>My Profile</li><li>My Subscription</li><li>Privacy policy</li><li>Terms &amp; Conditions</li></ul>
  </div>

  <div class="foot-col contact">
    <h4>Contact us</h4>
    <div class="contact-row" style="margin-top:26px"><svg width="14" height="13" viewBox="0 0 14 13" fill="none" stroke="#eee" stroke-width="1.5"><path d="M1 6l6-5 6 5v6H1z"/></svg><span>9 Wattle Court, Kelmvale<br>Western Australia.<br>ZipCode: 12345</span></div>
    <div class="contact-row"><svg width="14" height="12" viewBox="0 0 14 12" fill="#eee"><path d="M0 3c0-2 2-3 7-3s7 1 7 3v2h-3V3H3v2H0z"/><rect x="2" y="6" width="10" height="6"/></svg><span>123 555 0190</span></div>
    <div class="contact-row"><svg width="14" height="11" viewBox="0 0 14 11" fill="none" stroke="#eee" stroke-width="1.4"><rect x="1" y="1" width="12" height="9"/><path d="M1 1l6 5 6-5"/></svg><span>info@lodgivo.com</span></div>
  </div>

  <div class="foot-col quick">
    <h4>Quick Contact</h4>
    <div class="fields"><div class="field">Name</div><div class="field">Phone</div></div>
    <div class="field msg">Message</div>
    <div class="btn-send">Send</div>
  </div>
</footer>

<div class="abs bottom-bar">
  <span>CopyRight © 2019 Lodgivo. All Right Reserve</span>
  <div class="cards"><i></i><i></i><i></i><i></i><i></i></div>
</div>

</body>
</html>
```